Cat-products company needs smart, yet endearing, business card

We need a business card design for a new, but up-and-running, business based in Honolulu, Hawaii. The business is Purrnest Nook Co. Our first product is the most environmentally-friendly cat grass kit ever seen on the planet. Future products, currently in the R&D phase, will include a variety of exciting cat scratchers. We also do consulting work to help apartment-dwellers make their home more cat-friendly and, in the future, plan on doing full, custom installs of structure to create high walkways for cats.

Target Market(s)

Middle-aged, apartment-dwelling, middle-class workers who own 1 or more cats and who dote on them.

Industry/Entity Type

Pet Care

Contact Information for Business Card

A striking, professional, yet warm and friendly design is what we're after.

Font styles to use
Serif
Sans Serif
Other font styles liked:
• Comfortaa

Colors

Designer to choose colors to be used in the design.

Requirements
Must have
• The company logo: (see attachment)
• The company name: Purrnest Nook Co
• The web address: www.purrnestnookco.com
• Email: support@purrnestnookco.com
• Phone: +1 (808) 571 6023
• Update (Fri Jun 30 3017 7:45pm Hawaii Time) I would like, is possible, uploaded picture of the cat grass kit on the back of the card with some text along the lines of: Purrnest Nook Co - Maker Of The Leafiest Feline Sprout Set Yet
Nice to have
• A cat picture, cartoon, real or silhouette that illustrates cats in action and/or relaxing; ie using the apartment space to live, play and relax in and being well-contented.
• Most of the website is done in the font: Comfortaa. It might be nice to continue using this for brand consistency.
Should not have
• Hard-to-read fonts.

```html
<!DOCTYPE html>
<html lang="en">
<head>
<meta charset="utf-8">
<title>Purrnest Nook Co — Business Card</title>
<link rel="stylesheet" href="https://fonts.googleapis.com/css2?family=Comfortaa:wght@400;700&display=swap">
<style>
  :root {
    --bg: #e6e4e1;
    --card: #ffffff;
    --brown: #4e2a22;
    --amber: #f5a812;
    --ink: #3a3a3a;
    --muted: #6b6b6b;
    --rule: #8a8a8a;
  }
  * { box-sizing: border-box; margin: 0; padding: 0; }
  html, body {
    width: 1200px; height: 1000px; overflow: hidden;
    background: var(--bg);
    font-family: "Comfortaa", sans-serif;
  }
  .stage {
    position: relative; width: 1200px; height: 1000px;
  }
  .card {
    position: absolute; left: 250px; width: 700px; height: 400px;
    background: var(--card);
    box-shadow: 0 6px 18px rgba(0,0,0,0.12);
  }
  .card--front { top: 70px; }
  .card--back { top: 530px; }

  .brand {
    display: flex; align-items: center; gap: 12px;
    color: var(--brown); font-weight: 700; white-space: nowrap;
  }
  .brand__mark {
    width: 26px; height: 26px; background: var(--amber);
  }
  .card--front .brand {
    position: absolute; left: 50%; top: 50%;
    transform: translate(-50%, -50%);
    font-size: 40px;
  }
  .card--front .brand__mark { width: 34px; height: 34px; }
  .card--back .brand {
    position: absolute; right: 40px; top: 50px; font-size: 26px;
  }

  .rule { position: absolute; height: 1px; background: var(--rule); }
  .rule--upper { left: 300px; right: 40px; top: 228px; }
  .rule--lower { left: 40px; right: 40px; top: 322px; }

  .person { position: absolute; left: 40px; top: 252px; }
  .person__name { color: var(--amber); font-size: 32px; font-weight: 700; }
  .person__role { color: var(--muted); font-size: 20px; margin-top: 6px; }

  .contact {
    position: absolute; display: flex; align-items: center; gap: 8px;
    font-size: 15px; color: var(--ink); white-space: nowrap;
  }
  .contact svg { width: 16px; height: 16px; flex: none; }
  .contact--email { left: 330px; top: 246px; }
  .contact--web { left: 330px; top: 276px; color: var(--amber); }
  .contact--web .tld { color: var(--ink); }
  .contact--phone { left: 40px; top: 338px; }
  .contact--address { left: 40px; top: 366px; font-size: 17px; }
  .contact--address .label { color: var(--amber); }
</style>
</head>
<body>
<main class="stage">
  <section class="card card--front" aria-label="Card front">
    <div class="brand"><span class="brand__mark"></span>Purrnest Nook Co</div>
  </section>

  <section class="card card--back" aria-label="Card back">
    <div class="brand"><span class="brand__mark"></span>Purrnest Nook Co</div>

    <div class="rule rule--upper"></div>

    <div class="person">
      <p class="person__name">Leilani Kahale</p>
      <p class="person__role">Director</p>
    </div>

    <p class="contact contact--email">
      <svg viewBox="0 0 16 16" aria-hidden="true"><rect x="1" y="3" width="14" height="10" fill="#f5a812"/><path d="M1 3l7 6 7-6" fill="none" stroke="#fff" stroke-width="1.4"/></svg>
      support@purrnestnookco.com
    </p>
    <p class="contact contact--web">
      <svg viewBox="0 0 16 16" aria-hidden="true"><g fill="none" stroke="#f5a812" stroke-width="1.3"><circle cx="8" cy="8" r="6.5"/><ellipse cx="8" cy="8" rx="3" ry="6.5"/><path d="M1.5 8h13M2.5 4.8h11M2.5 11.2h11"/></g></svg>
      <span>www.purrnestnookco<span class="tld">.com</span></span>
    </p>

    <div class="rule rule--lower"></div>

    <p class="contact contact--phone">
      <svg viewBox="0 0 16 16" aria-hidden="true"><path d="M4 1.5l2.5 3-1.6 1.8c.9 2 2.4 3.5 4.4 4.4l1.8-1.6 3 2.5-1.6 2.4C7.5 13.8 2.2 8.5 1.6 3.1z" fill="#f5a812"/></svg>
      +1 (808) 571 6023
    </p>
    <p class="contact contact--address">
      <span><span class="label">Address</span> - Your Street Address, Country,1234</span>
    </p>
  </section>
</main>
</body>
</html>
```